design a construction company business card

Design business card around our logo. Card must have all the typical info: name, title, address, phone, email, business name, etc. Somewhere on the card I would like to see our motto "Rooted in trust... Driven by craftsmanship." Consider adding a splash of bright orange to the card to complement the blues and silvers/grays in the logo. We are open to metallic inks, textures, etc. We would like to see options on both light and dark backgrounds. The font in the logo is Euro Technic Extended Regular.

```html
<!DOCTYPE html>
<html lang="en">
<head>
<meta charset="utf-8">
<title>Halvorsen Builders – Business Card</title>
<link rel="stylesheet" href="https://fonts.googleapis.com/css2?family=Roboto:ital,wght@0,400;0,700;1,400&display=swap">
<style>
  :root {
    --page-bg: #e4e4e4;
    --blue-deep: #283a92;
    --blue-mid: #1f5cb0;
    --blue-light: #1576c4;
    --steel: #818286;
    --white: #ffffff;
    --ink-grey: #55575b;
    --card-shadow: 0 2px 4px rgba(0,0,0,0.35);
  }
  * { box-sizing: border-box; margin: 0; padding: 0; }
  html, body {
    width: 1125px; height: 1200px; overflow: hidden;
    background: var(--page-bg);
    font-family: "Roboto", Arial, sans-serif;
  }
  .card {
    position: absolute; left: 171px; width: 826px; height: 472px;
    box-shadow: var(--card-shadow); overflow: hidden;
  }
  .card--front {
    top: 106px;
    background: radial-gradient(circle at 45% 48%, var(--blue-light) 0%, var(--blue-mid) 35%, var(--blue-deep) 80%);
    color: var(--white);
  }
  .card--back { top: 639px; background: var(--white); }

  .brand-name {
    position: absolute; left: 60px; top: 70px;
    display: flex; align-items: center; gap: 12px;
    font-weight: 700; font-size: 40px; letter-spacing: 1px; line-height: 1;
  }
  .brand-name__square { width: 18px; height: 18px; background: var(--white); }
  .brand-sub {
    position: absolute; left: 60px; top: 122px;
    font-weight: 700; font-size: 20px; letter-spacing: 2px;
  }

  .person { position: absolute; left: 60px; top: 200px; }
  .person__name { font-weight: 700; font-size: 28px; line-height: 1.1; }
  .person__title { font-size: 19px; margin-top: 6px; letter-spacing: 0.5px; }

  .address { position: absolute; left: 60px; top: 274px; font-size: 18px; line-height: 25px; letter-spacing: 0.4px; }

  .contact { position: absolute; left: 60px; top: 336px; list-style: none; font-size: 17.5px; }
  .contact li { display: flex; align-items: center; gap: 9px; height: 26px; }
  .contact svg { width: 18px; height: 18px; fill: var(--white); }

  .skyline-area { position: absolute; left: 340px; top: 140px; width: 258px; height: 332px; }
  .steel-band { position: absolute; left: 598px; top: 0; width: 228px; height: 472px; background: var(--steel); }

  .back-brand {
    position: absolute; left: 0; right: 0; top: 205px;
    display: flex; align-items: center; justify-content: center; gap: 14px;
    color: var(--blue-mid); font-weight: 700; font-size: 42px; letter-spacing: 1px;
  }
  .back-brand__square { width: 20px; height: 20px; background: var(--blue-mid); }
  .back-brand-sub {
    position: absolute; left: 0; right: 0; top: 268px; text-align: center;
    color: var(--blue-mid); font-weight: 700; font-size: 21px; letter-spacing: 3px;
  }
  .motto {
    position: absolute; left: 0; right: 0; top: 400px; text-align: center;
    font-style: italic; font-size: 20px; color: var(--ink-grey);
  }
</style>
</head>
<body>
  <section class="card card--front">
    <div class="brand-name"><span class="brand-name__square"></span>HALVORSEN</div>
    <div class="brand-sub">BUILDERS, INC.</div>

    <div class="person">
      <div class="person__name">DANIEL REYES</div>
      <div class="person__title">CEO/FOUNDER</div>
    </div>

    <div class="address">2140 Birchwood Drive<br>Juneau, Alaska 99801</div>

    <ul class="contact">
      <li><svg viewBox="0 0 24 24"><path d="M6.6 10.8a15.1 15.1 0 0 0 6.6 6.6l2.2-2.2c.3-.3.7-.4 1-.2 1.1.4 2.3.6 3.6.6.6 0 1 .4 1 1V20c0 .6-.4 1-1 1C10.6 21 3 13.4 3 4c0-.6.4-1 1-1h3.5c.6 0 1 .4 1 1 0 1.3.2 2.5.6 3.6.1.3 0 .7-.2 1z"/></svg>555 218 4790</li>
      <li><svg viewBox="0 0 24 24"><path d="M2 5h20v14H2zm2 2v.5l8 5 8-5V7zm0 3v7h16v-7l-8 5z"/></svg>dan@halvor.com</li>
      <li><svg viewBox="0 0 24 24"><circle cx="12" cy="12" r="10"/></svg>www.halvor.com</li>
    </ul>

    <svg class="skyline-area" role="img" aria-label="Large skyline symbol of the company mark" viewBox="0 0 258 332" preserveAspectRatio="none">
      <defs>
        <linearGradient id="skyline-fill" x1="0" y1="0" x2="0" y2="1">
          <stop offset="0" stop-color="#ffffff" stop-opacity="0.15"/>
          <stop offset="1" stop-color="#ffffff" stop-opacity="0.55"/>
        </linearGradient>
      </defs>
      <rect width="258" height="332" fill="url(#skyline-fill)"/>
    </svg>
    <div class="steel-band"></div>
  </section>

  <section class="card card--back">
    <div class="back-brand"><span class="back-brand__square"></span>HALVORSEN</div>
    <div class="back-brand-sub">BUILDERS, INC.</div>
    <p class="motto">Rooted in trust... Driven by craftsmanship.</p>
  </section>
</body>
</html>
```